Tech business card design

We need an amazing business card design for our new business 'Pexla' a marketing tech startup based in Sydney, Australia. We provide an online marketplace for businesses to search and buy advertising media, connect with service providers and learn more about marketing. We wish to communicate 'cool tech', reliability and professionalism and design based around our logo.

Target Market(s)

Business Owners

Contact Information for Business Card

Name
Position
Email Address
Website
Phone Number

Font styles to use
Other font styles liked:
• Avenir & Avenir Next

Colors

Designer to choose colors to be used in the design.

```html
<!DOCTYPE html>
<html lang="en">
<head>
<meta charset="utf-8">
<title>Pexla Business Card</title>
<link href="https://fonts.googleapis.com/css2?family=Mulish:wght@400;700;900&display=swap" rel="stylesheet">
<style>
  :root {
    --backdrop: #e1dede;
    --card: #ffffff;
    --card-edge: #2a2a2a;
    --navy: #14123a;
    --rule: #2c2a55;
  }
  * { margin: 0; padding: 0; box-sizing: border-box; }
  html, body { width: 975px; height: 1200px; overflow: hidden; }
  body {
    background: var(--backdrop);
    font-family: "Mulish", "Avenir Next", Avenir, sans-serif;
    color: var(--navy);
    position: relative;
  }
  .card {
    position: absolute;
    left: 56px;
    width: 864px;
    height: 496px;
    background: var(--card);
    border: 1px solid var(--card-edge);
    border-radius: 38px;
  }
  .card--front { top: 90px; }
  .card--back { top: 635px; }
  .wordmark {
    position: absolute;
    font-weight: 900;
    font-size: 148px;
    line-height: 1;
    letter-spacing: -2px;
    color: var(--navy);
  }
  .card--front .wordmark { right: 30px; top: 54px; }
  .card--back .wordmark { left: 0; right: 0; text-align: center; top: 178px; }
  .holder-name {
    position: absolute; left: 48px; top: 236px;
    font-weight: 700; font-size: 28px; letter-spacing: 0.2px;
  }
  .holder-role {
    position: absolute; left: 48px; top: 270px;
    font-size: 23px;
  }
  .divider {
    position: absolute; left: 49px; top: 302px;
    width: 787px; height: 3px; background: var(--rule);
  }
  .contact-list {
    position: absolute; left: 49px; top: 330px;
    list-style: none; font-size: 21px;
  }
  .contact-list li {
    display: flex; align-items: center; gap: 9px;
    height: 32.5px;
  }
  .contact-list svg { width: 21px; height: 21px; flex: none; }
  .address {
    position: absolute; left: 604px; top: 348px;
    font-size: 21px; line-height: 28px;
  }
  .back-url {
    position: absolute; left: 0; right: 0; top: 402px;
    text-align: center; font-size: 27px; letter-spacing: 4px;
  }
</style>
</head>
<body>
  <section class="card card--front">
    <div class="wordmark">Pexla</div>
    <h1 class="holder-name">JOHN SMITH</h1>
    <p class="holder-role">Position</p>
    <div class="divider"></div>
    <ul class="contact-list">
      <li>
        <svg viewBox="0 0 24 24" aria-hidden="true"><circle cx="12" cy="12" r="10.5" fill="none" stroke="currentColor" stroke-width="2"/><path d="M8.3 6.5l1.8 0 1 2.8-1.3 1.1c.7 1.5 1.9 2.7 3.4 3.4l1.1-1.3 2.8 1v1.8c0 .6-.5 1-1.1 1-4.4-.3-8.5-4.4-8.8-8.8 0-.6.4-1 1.1-1z" fill="currentColor"/></svg>
        012-345-6789
      </li>
      <li>
        <svg viewBox="0 0 24 24" aria-hidden="true"><rect x="1.5" y="5" width="21" height="14" fill="currentColor"/><path d="M1.5 5l10.5 8 10.5-8M1.5 19l8-7M22.5 19l-8-7" fill="none" stroke="#fff" stroke-width="1.6"/></svg>
        info@pexla.com
      </li>
      <li>
        <svg viewBox="0 0 24 24" aria-hidden="true"><g fill="none" stroke="currentColor" stroke-width="1.6"><circle cx="12" cy="12" r="10"/><ellipse cx="12" cy="12" rx="4.5" ry="10"/><path d="M2 12h20M3.5 7h17M3.5 17h17M12 2v20"/></g></svg>
        www.pexla.com
      </li>
    </ul>
    <address class="address" style="font-style:normal">Street name City Name,<br>Zipcode,012345</address>
  </section>

  <section class="card card--back">
    <div class="wordmark">Pexla</div>
    <p class="back-url">www.pexla.com</p>
  </section>
</body>
</html>
```